Harbourline Electrical Solutions

On one side. LOGO (underneath:) Commercial Industrial Residential

- NAME & CONTACT DETAILS

Marcus T. Hollings
Project Manager

(Cell icon) (441) 555-0187
(Email icon) hlelectricalsolutions@mailvento.com
(Facebook & Instagram icons )@hlelectricalsolutions

Other side: LOGO - underneath ELECTRICAL CONSTRUCTION & MAINTENANCE . LED LIGHTING & AUTOMATION . LIFE SAFETY SYSTEMS (FIRE ALARM / SECURITY) . DATA & COMMUNICATION

```html
<!DOCTYPE html>
<html lang="en">
<head>
<meta charset="utf-8">
<title>Harbourline Electrical Solutions – Business Card</title>
<link href="https://fonts.googleapis.com/css2?family=Montserrat:wght@300;400;500;600;700&display=swap" rel="stylesheet">
<style>
  :root {
    --teal: #10566b;
    --ink: #2f3338;
    --paper: #ffffff;
    --backdrop: #2b2b2e;
  }
  * { margin: 0; padding: 0; box-sizing: border-box; }
  html, body { width: 1200px; height: 1200px; overflow: hidden; }
  body {
    background: var(--backdrop);
    font-family: "Montserrat", sans-serif;
    position: relative;
  }
  .card {
    position: absolute;
    left: 292px;
    width: 599px;
    height: 359px;
  }
  .card--front { top: 220px; background: var(--teal); color: var(--paper); }
  .card--back { top: 632px; background: var(--paper); }

  /* Brand lockup */
  .brand {
    position: absolute;
    display: flex;
    align-items: center;
  }
  .brand__mark { flex: none; }
  .brand__name {
    font-weight: 500;
    text-transform: uppercase;
    line-height: 1.12;
  }
  .card--front .brand {
    left: 50%; top: 177px;
    transform: translate(-50%, -50%);
    gap: 18px;
  }
  .card--front .brand__mark { width: 34px; height: 34px; background: var(--paper); }
  .card--front .brand__name { font-size: 20px; letter-spacing: 2.4px; color: var(--paper); }

  .services {
    position: absolute;
    left: 0; right: 0; top: 300px;
    text-align: center;
    font-size: 11.2px;
    font-weight: 300;
    line-height: 16px;
    letter-spacing: 0.1px;
    text-transform: uppercase;
  }

  /* Back */
  .card--back .brand { left: 62px; top: 140px; gap: 10px; }
  .card--back .brand__mark { width: 22px; height: 22px; background: var(--teal); }
  .card--back .brand__name { font-size: 12.5px; letter-spacing: 1.6px; color: var(--teal); }
  .sectors {
    position: absolute;
    left: 62px; top: 204px;
    font-size: 7.6px;
    font-weight: 500;
    letter-spacing: 1.8px;
    color: var(--ink);
    text-transform: uppercase;
  }
  .sectors .sep { color: var(--teal); padding: 0 4px; }
  .divider {
    position: absolute;
    left: 295px; top: 132px;
    width: 1.2px; height: 97px;
    background: var(--teal);
  }
  .contact { position: absolute; left: 309px; top: 130px; color: var(--ink); }
  .contact__name {
    font-size: 16.5px; font-weight: 700; color: var(--teal);
    text-transform: uppercase; letter-spacing: 0.2px;
  }
  .contact__role { font-size: 11px; font-weight: 500; margin-top: -1px; }
  .contact__list { list-style: none; margin-top: 11px; }
  .contact__list li {
    display: flex; align-items: center; gap: 4px;
    font-size: 12px; height: 19px; letter-spacing: 0.3px;
  }
  .icon { width: 12px; height: 12px; flex: none; }
</style>
</head>
<body>

<section class="card card--front">
  <div class="brand">
    <span class="brand__mark"></span>
    <div class="brand__name">Harbourline<br>Electrical<br>Solutions</div>
  </div>
  <p class="services">
    Electrical Construction &amp; Maintenance &bull; LED Lighting &amp; Automation<br>
    &bull; Life Safety Systems (Fire Alarm / Security) &bull; Data &amp; Communication
  </p>
</section>

<section class="card card--back">
  <div class="brand">
    <span class="brand__mark"></span>
    <div class="brand__name">Harbourline<br>Electrical<br>Solutions</div>
  </div>
  <p class="sectors">Commercial<span class="sep">|</span>Industrial<span class="sep">|</span>Residential</p>
  <div class="divider"></div>
  <div class="contact">
    <h1 class="contact__name">Marcus T. Hollings</h1>
    <p class="contact__role">Project Manager</p>
    <ul class="contact__list">
      <li>
        <svg class="icon" viewBox="0 0 12 12" aria-hidden="true">
          <circle cx="6" cy="6" r="5.4" fill="none" stroke="var(--teal)" stroke-width="0.9"/>
          <path d="M4 3.2l1 1.2-.6.7c.4.9 1 1.5 1.9 1.9l.7-.6 1.2 1-.6.9c-2 0-4.4-2.4-4.4-4.4z" fill="var(--teal)"/>
        </svg>
        (441) 555-0187
      </li>
      <li>
        <svg class="icon" viewBox="0 0 12 12" aria-hidden="true">
          <circle cx="6" cy="6" r="5.4" fill="none" stroke="var(--teal)" stroke-width="0.9"/>
          <rect x="3.3" y="4" width="5.4" height="4" fill="none" stroke="var(--teal)" stroke-width="0.8"/>
          <path d="M3.3 4l2.7 2.2L8.7 4" fill="none" stroke="var(--teal)" stroke-width="0.8"/>
        </svg>
        hlelectricalsolutions@mailvento.com
      </li>
      <li>
        <svg class="icon" viewBox="0 0 12 12" aria-hidden="true">
          <circle cx="6" cy="6" r="5.4" fill="none" stroke="var(--teal)" stroke-width="0.9"/>
        </svg>
        <svg class="icon" viewBox="0 0 12 12" aria-hidden="true" style="margin-left:5px">
          <circle cx="6" cy="6" r="5.4" fill="none" stroke="var(--teal)" stroke-width="0.9"/>
        </svg>
        @hlelectricalsolutions
      </li>
    </ul>
  </div>
</section>

</body>
</html>
```